Business Card for Multi-Brand Sportswear Company

We are looking for a business card which represents our company and the multiple brands within it.

The company: Fen Athletics (LTD)
The brands: Fen, TavaPuni, ElmStretch, Grit and Rain

Employees using these cards would be representing Fen Athletics, rather than any of the individual brands. You will see a current design within the uploaded files, to give some inspiration. The actual text of the brands is not necessary, but the logos should be on there is some format.

Our creative minds on this are stretched, so we are looking for someone to make this their own, and show us what a good business card should look like.

We may like to get these printed with spot gloss, so keep that in mind with your designs.

www.fenathletics.co.uk

Industry/Entity Type

Business

Contact Information for Business Card

Leo Pemberton-Hale
Operations Manager
(+44) 1632 960 418
Leo@fenathletics.co.uk
www.fenathletics.co.uk

Font styles to use
Sans Serif
Other font styles liked:
• Eurostile

Colors
ffffff

Requirements
Nice to have
• Dark (black) background

```html
<!DOCTYPE html>
<html lang="en">
<head>
<meta charset="utf-8">
<title>Fen Athletics Business Card</title>
<link rel="stylesheet" href="https://fonts.googleapis.com/css2?family=Exo+2:wght@400;500;600;700&display=swap">
<style>
  :root {
    --page-bg: #ececec;
    --card-dark: #2a2a2a;
    --card-mid: #333333;
    --card-deep: #222222;
    --white: #ffffff;
    --soft-white: #e6e6e6;
    --brand-red: #d0202a;
    --muted: #8c8c8c;
  }
  * { box-sizing: border-box; margin: 0; padding: 0; }
  html, body {
    width: 1200px; height: 586px; overflow: hidden;
    background: var(--page-bg);
    font-family: "Exo 2", sans-serif;
    color: var(--white);
  }
  .card {
    position: absolute; top: 129px;
    width: 501px; height: 301px;
    overflow: hidden;
  }
  .card--front { left: 66px; }
  .card--back { left: 608px; }
  .card__texture {
    position: absolute; inset: 0;
    background: linear-gradient(135deg, var(--card-mid) 0%, var(--card-dark) 45%, var(--card-deep) 100%);
  }
  .wordmark { position: absolute; text-align: right; }
  .wordmark__name {
    display: block; font-weight: 700; color: var(--white);
    letter-spacing: 1px; line-height: 1; white-space: nowrap;
  }
  .wordmark__tagline {
    display: block; font-weight: 400; color: var(--soft-white);
    letter-spacing: 2.5px; text-transform: uppercase; white-space: nowrap;
  }
  .card--front .wordmark { left: 0; right: 0; top: 92px; text-align: center; }
  .card--front .wordmark__name { font-size: 58px; }
  .card--front .wordmark__tagline { font-size: 12px; margin-top: 8px; letter-spacing: 3px; }
  .card--back .wordmark { left: 0; right: 0; top: 24px; text-align: center; }
  .card--back .wordmark__name { font-size: 34px; }
  .card--back .wordmark__tagline { font-size: 8px; margin-top: 4px; }

  .brand-row {
    position: absolute; left: 0; right: 0;
    display: flex; justify-content: center; align-items: center; gap: 12px;
    font-weight: 600; color: var(--muted); white-space: nowrap;
  }
  .card--front .brand-row { top: 244px; font-size: 12px; }
  .card--back .brand-row { top: 274px; font-size: 10px; gap: 10px; }
  .brand-row__item--fen { color: var(--white); }

  .side-bar {
    position: absolute; top: 58px; width: 15px; height: 185px;
    background: var(--brand-red);
  }
  .side-bar--left { left: 0; border-radius: 0 10px 10px 0; }
  .side-bar--right { right: 0; border-radius: 10px 0 0 10px; }

  .person { position: absolute; right: 277px; top: 165px; text-align: right; }
  .person__name { font-size: 17px; font-weight: 700; letter-spacing: .3px; }
  .person__role { font-size: 12px; font-weight: 400; color: var(--soft-white); margin-top: 4px; }

  .divider {
    position: absolute; left: 234px; top: 127px; width: 2px; height: 112px;
    background: linear-gradient(to bottom, transparent, var(--brand-red) 50%, transparent);
  }

  .contact { position: absolute; left: 260px; top: 127px; list-style: none; }
  .contact__line {
    display: flex; align-items: center; gap: 7px;
    font-size: 12px; height: 24px; color: var(--soft-white);
  }
  .contact__icon { width: 13px; height: 13px; flexed: none; fill: var(--brand-red); }
  .address {
    position: absolute; left: 265px; top: 199px;
    font-size: 12.5px; font-weight: 600; line-height: 17px; font-style: normal;
  }
</style>
</head>
<body>

<section class="card card--front">
  <div class="card__texture" role="img" aria-label="Dark faceted geometric texture"></div>
  <div class="wordmark">
    <span class="wordmark__name">Fen Athletics</span>
    <span class="wordmark__tagline">Performance Wear</span>
  </div>
  <div class="brand-row">
    <span class="brand-row__item">ElmStretch</span>
    <span class="brand-row__item">Grit and Rain</span>
    <span class="brand-row__item">TavaPuni</span>
    <span class="brand-row__item brand-row__item--fen">Fen</span>
  </div>
</section>

<section class="card card--back">
  <div class="card__texture" role="img" aria-label="Dark faceted geometric texture"></div>
  <div class="side-bar side-bar--left"></div>
  <div class="side-bar side-bar--right"></div>

  <div class="wordmark">
    <span class="wordmark__name">Fen Athletics</span>
    <span class="wordmark__tagline">Performance Wear</span>
  </div>

  <div class="person">
    <p class="person__name">Owen Brackley</p>
    <p class="person__role">Managing Director</p>
  </div>

  <div class="divider"></div>

  <ul class="contact">
    <li class="contact__line">
      <svg class="contact__icon" viewBox="0 0 16 16" aria-hidden="true"><path d="M1 5c0-2 2-3 7-3s7 1 7 3v1h-4V4.5H5V6H1zM3 7h10l2 7H1z"/></svg>
      +44 (0)1632 960418
    </li>
    <li class="contact__line">
      <svg class="contact__icon" viewBox="0 0 16 16" aria-hidden="true"><path d="M4 1h8v4H4zM1 6h14v6h-3v3H4v-3H1zM5 10v4h6v-4z"/></svg>
      (555) 014-2290
    </li>
    <li class="contact__line">
      <svg class="contact__icon" viewBox="0 0 16 16" aria-hidden="true"><path d="M1 3h14v10H1zM2.5 4.5 8 9l5.5-4.5z" fill-rule="evenodd"/></svg>
      owen@fenathletics.co.uk
    </li>
  </ul>

  <address class="address">
    Low Meadow, Ashby<br>
    Hexford, HX4 2QL
  </address>

  <div class="brand-row">
    <span class="brand-row__item">ElmStretch</span>
    <span class="brand-row__item">Grit and Rain</span>
    <span class="brand-row__item">TavaPuni</span>
    <span class="brand-row__item brand-row__item--fen">Fen</span>
  </div>
</section>

</body>
</html>
```